Business Card for premium dental clinic

We are a premium dental clinic based in Brasov, Romania with more than 15 year on the market, providing quality dental treatment made by a team of more specialized dentists, working with modern equipment as a solution to beautiful and healthy teeth.

Our current logo for the clinic use 2 square with colors black and gold - dr Ternisu - studio, using family fonts Bodoni, Myriad Pro and Segoe Print.
Depending on the printing we used some gold CMYK background or gold foil picture background or a gold gradient.
We want a business card:
- eye catching business card
- distinguished business card
- premium design
- to keep the color scheme of black and gold
- to attract the customers to spent time reading the information
- modern concept

```html
<!DOCTYPE html>
<html lang="en">
<head>
<meta charset="utf-8">
<title>dr Ternisu – Business Card</title>
<link rel="stylesheet" href="https://fonts.googleapis.com/css2?family=Montserrat:wght@400;500;600&display=swap">
<style>
  :root {
    --page-bg: #e9e6e0;
    --charcoal: #2b2e31;
    --gold: #c9a62c;
    --gold-text: #c49a2a;
    --ink: #111111;
    --paper: #fbfbfa;
    --muted: #6b6b6b;
  }
  * { box-sizing: border-box; margin: 0; padding: 0; }
  html, body { width: 1200px; height: 866px; overflow: hidden; }
  body {
    background: var(--page-bg);
    font-family: "Montserrat", sans-serif;
    position: relative;
  }
  .card {
    position: absolute;
    width: 560px;
    height: 320px;
    box-shadow: 0 14px 30px rgba(0,0,0,0.22);
    overflow: hidden;
  }

  /* Front side */
  .card-front { left: 50px; top: 70px; display: flex; }
  .front-dark { width: 36%; background: var(--charcoal); }
  .front-gold {
    flex: 1;
    background: var(--gold);
    display: flex;
    align-items: center;
    justify-content: center;
    gap: 14px;
  }
  .brand-square {
    width: 22px; height: 22px;
    background: var(--ink);
  }
  .brand-name {
    font-size: 40px;
    font-weight: 500;
    color: var(--ink);
    letter-spacing: 0.5px;
  }

  /* Back side */
  .card-back {
    left: 590px; top: 476px;
    background: var(--paper);
    display: flex;
    align-items: center;
  }
  .back-brand {
    width: 262px;
    display: flex;
    align-items: center;
    justify-content: center;
    gap: 10px;
    padding-top: 60px;
  }
  .back-brand .brand-square { width: 16px; height: 16px; background: var(--gold); }
  .back-brand .brand-name { font-size: 27px; color: var(--ink); }
  .divider {
    width: 2px; height: 150px;
    background: var(--gold);
  }
  .details { padding-left: 38px; padding-bottom: 20px; }
  .person-name {
    font-size: 21px;
    font-weight: 600;
    color: var(--gold-text);
    letter-spacing: 1px;
    text-transform: uppercase;
  }
  .person-role {
    font-size: 15px;
    color: var(--muted);
    margin-top: 2px;
    margin-bottom: 18px;
  }
  .contact-list { list-style: none; }
  .contact-list li {
    display: flex;
    align-items: center;
    gap: 12px;
    font-size: 14px;
    color: #333;
    line-height: 24px;
  }
  .contact-list svg { width: 14px; height: 14px; flex: none; }
</style>
</head>
<body>

  <section class="card card-front" aria-label="Card front">
    <div class="front-dark"></div>
    <div class="front-gold">
      <span class="brand-square"></span>
      <span class="brand-name">dr Ternisu</span>
    </div>
  </section>

  <section class="card card-back" aria-label="Card back">
    <div class="back-brand">
      <span class="brand-square"></span>
      <span class="brand-name">dr Ternisu</span>
    </div>
    <div class="divider"></div>
    <div class="details">
      <h1 class="person-name">Mara Ionescu</h1>
      <p class="person-role">Doctor</p>
      <ul class="contact-list">
        <li>
          <svg viewBox="0 0 16 16" aria-hidden="true"><path d="M4 1.5l2.2 3-1.4 1.6c.8 1.9 2.2 3.3 4.1 4.1l1.6-1.4 3 2.2-1.2 2.5C6.5 13.3 2.7 9.5 1.5 3z" fill="var(--gold)"/></svg>
          +40 268 555 019
        </li>
        <li>
          <svg viewBox="0 0 16 16" aria-hidden="true"><rect x="1" y="3" width="14" height="10" fill="var(--gold)"/><path d="M1 3l7 6 7-6" fill="none" stroke="#fff" stroke-width="1.2"/></svg>
          m.ionescu@drternisu.ro
        </li>
        <li>
          <svg viewBox="0 0 16 16" aria-hidden="true"><g fill="none" stroke="var(--gold)" stroke-width="1.3"><circle cx="8" cy="8" r="6.5"/><ellipse cx="8" cy="8" rx="2.8" ry="6.5"/><path d="M1.5 8h13M2.5 4.8h11M2.5 11.2h11"/></g></svg>
          www.drternisu.ro
        </li>
      </ul>
    </div>
  </section>

</body>
</html>
```